Summit Ridge Business Card

Side 1: Summit Ridge Logo (logo without Maltese cross) with industrial rope rescue related theme. Our company services - TRAINING - Fire Training, Confined Space Rescue Training, Rope Rescue training, Hazmat Training, Incident Command, EMS, Pump Operations Training. Website - summitridgeexample.com.
Side 2: Summit Ridge Fire Department Logo (logo with Maltese cross) with Firefighter related theme. Company (division) services - FIELD SERVICES - Fire Department, Stand-by Rescue, Safety, EMS, Planning. "Supporting the Emergency Response Community Since 1967"

Add contact information wherever it makes since (Name, Email, Phone).
I would like it to represent the Summit Ridge Fire Department Logo as a division not as a separate entity without saying it, possibly by depicting it in the background of Side 2 instead of being a standalone picture like the logo on Side 1.

```html
<!DOCTYPE html>
<html lang="en">
<head>
<meta charset="utf-8">
<title>Summit Ridge Business Card</title>
<link rel="stylesheet" href="https://fonts.googleapis.com/css2?family=Montserrat:wght@500;600;700;800&family=Poppins:wght@400;500;600&display=swap">
<style>
  :root {
    --red: #f50a0a;
    --charcoal: #3a3b3e;
    --ink: #1d1d1f;
    --white: #ffffff;
    --stage: #e9e9eb;
  }
  * { box-sizing: border-box; margin: 0; padding: 0; }
  html, body { width: 1200px; height: 1015px; overflow: hidden; }
  body {
    background: var(--stage);
    font-family: "Montserrat", sans-serif;
    color: var(--ink);
    position: relative;
  }
  .card {
    position: absolute;
    left: 190px;
    width: 820px;
    height: 468px;
    background: var(--white);
    overflow: hidden;
    box-shadow: 0 6px 18px rgba(0,0,0,.18);
  }
  .card--training { top: 26px; }
  .card--field { top: 521px; }

  .footer-band { position: absolute; left: 0; bottom: 0; width: 820px; height: 82px; }
  .footer-band svg { display: block; }
  .footer-text {
    position: absolute;
    bottom: 0;
    height: 82px;
    display: flex;
    align-items: center;
    color: var(--white);
    white-space: nowrap;
  }

  .wordmark {
    position: absolute;
    display: flex;
    align-items: center;
    gap: 14px;
    white-space: nowrap;
  }
  .wordmark__dot { width: 24px; height: 24px; border-radius: 50%; background: var(--red); }
  .wordmark__name {
    font-family: "Montserrat", sans-serif;
    font-weight: 800;
    font-size: 36px;
    letter-spacing: 1px;
    text-transform: uppercase;
  }

  /* Side 1 */
  .card--training .wordmark { right: 50px; top: 46px; }
  .card--training .wordmark__name { color: var(--red); }
  .service-list {
    position: absolute;
    left: 70px;
    top: 124px;
    list-style: none;
  }
  .service-list li {
    font-family: "Montserrat", sans-serif;
    font-weight: 500;
    font-size: 18px;
    letter-spacing: 1px;
    text-transform: uppercase;
    line-height: 33px;
    display: flex;
    align-items: center;
    white-space: nowrap;
  }
  .service-list li::before {
    content: "";
    width: 9px; height: 9px;
    border-radius: 50%;
    background: var(--red);
    margin-right: 10px;
  }
  .website { left: 290px; font-family: "Poppins", sans-serif; font-size: 24px; letter-spacing: 2px; }

  /* Side 2 */
  .card--field .wordmark { right: 50px; top: 66px; }
  .card--field .wordmark__name { color: var(--ink); font-size: 32px; letter-spacing: 3px; }
  .contact { position: absolute; left: 60px; top: 86px; font-family: "Poppins", sans-serif; }
  .contact__name { font-weight: 600; font-size: 30px; letter-spacing: .5px; margin-bottom: 4px; }
  .contact__line { display: flex; align-items: center; gap: 10px; font-size: 22px; line-height: 30px; }
  .contact__line svg { flex: none; }
  .field-services {
    position: absolute;
    right: 50px;
    top: 232px;
    text-align: right;
    font-family: "Montserrat", sans-serif;
    font-weight: 800;
    font-size: 34px;
    letter-spacing: 1px;
    line-height: 44px;
    text-transform: uppercase;
    white-space: nowrap;
  }
  .field-services .sep { color: var(--red); padding: 0 6px; }
  .tagline { left: 205px; font-family: "Poppins", sans-serif; font-weight: 600; font-size: 18px; letter-spacing: .5px; }
</style>
</head>
<body>

<section class="card card--training" aria-label="Business card, training side">
  <div class="wordmark">
    <span class="wordmark__dot"></span>
    <span class="wordmark__name">Summit Ridge</span>
  </div>

  <ul class="service-list">
    <li>Fire Training</li>
    <li>Confined Space Rescue Training</li>
    <li>Rope Rescue Training</li>
    <li>Hazmat Training</li>
    <li>Incident Command</li>
    <li>EMS</li>
    <li>Pump Operations Training</li>
  </ul>

  <div class="footer-band">
    <svg width="820" height="82" viewBox="0 0 820 82" aria-hidden="true">
      <rect x="0" y="0" width="820" height="82" fill="var(--red)"/>
      <polygon points="0,0 120,0 175,82 0,82" fill="var(--charcoal)"/>
      <circle cx="105" cy="41" r="26" fill="var(--white)"/>
    </svg>
  </div>
  <div class="footer-text website">www.summitridgeexample.com</div>
</section>

<section class="card card--field" aria-label="Business card, field services side">
  <div class="contact">
    <p class="contact__name">Daniel Carter</p>
    <p class="contact__line">
      <svg width="20" height="20" viewBox="0 0 24 24" aria-hidden="true"><path fill="var(--red)" d="M6.6 10.8a15.1 15.1 0 0 0 6.6 6.6l2.2-2.2c.3-.3.7-.4 1-.2 1.1.4 2.3.6 3.6.6.6 0 1 .4 1 1V20c0 .6-.4 1-1 1A17 17 0 0 1 3 4c0-.6.4-1 1-1h3.5c.6 0 1 .4 1 1 0 1.3.2 2.5.6 3.6.1.3 0 .7-.2 1z"/></svg>
      044-555 010 234
    </p>
    <p class="contact__line">
      <svg width="20" height="16" viewBox="0 0 24 18" aria-hidden="true"><rect x="0" y="0" width="24" height="18" rx="2" fill="var(--red)"/><path d="M1 2l11 8 11-8" fill="none" stroke="var(--white)" stroke-width="2"/></svg>
      info@summitmail.com
    </p>
  </div>

  <div class="wordmark">
    <span class="wordmark__dot"></span>
    <span class="wordmark__name">Summit Ridge</span>
  </div>

  <p class="field-services">
    Fire Department<span class="sep">•</span>Stand-By Rescue<br>
    Safety<span class="sep">•</span>EMS<span class="sep">•</span>Planning
  </p>

  <div class="footer-band">
    <svg width="820" height="82" viewBox="0 0 820 82" aria-hidden="true">
      <rect x="0" y="0" width="820" height="82" fill="var(--red)"/>
      <polygon points="0,0 120,0 175,82 0,82" fill="var(--charcoal)"/>
      <circle cx="105" cy="41" r="26" fill="var(--white)"/>
    </svg>
  </div>
  <div class="footer-text tagline">Supporting the Emergency Response Community Since 1967</div>
</section>

</body>
</html>
```